Copper lark buildworks

Copper lark buildworks is a small construction company.
Who is a licenced builder, Carpenter, joiner,
working on heritage ,new build, speacial projects and sometimes furniture

Industry/Entity Type

Construction

```html
<!DOCTYPE html>
<html lang="en">
<head>
<meta charset="utf-8">
<title>Copper Lark Buildworks – Business Card</title>
<link rel="stylesheet" href="https://fonts.googleapis.com/css2?family=Open+Sans:wght@400;700&display=swap">
<style>
  :root {
    --page-bg: #ffffff;
    --green-deep: #035e2d;
    --green-mid: #0c7a3e;
    --green-bright: #2fab4a;
    --frame-line: #0a3a1d;
    --panel-edge: #1c8a3c;
    --panel-centre: #2b2c31;
    --panel-outer: #131316;
    --text-light: #ffffff;
  }
  html, body {
    margin: 0;
    padding: 0;
    width: 1200px;
    height: 1200px;
    overflow: hidden;
    background: var(--page-bg);
  }
  .canvas {
    position: relative;
    width: 1200px;
    height: 1200px;
  }
  .card-art {
    position: absolute;
    inset: 0;
  }
  .card-text {
    position: absolute;
    left: 0;
    width: 1200px;
    text-align: center;
    color: var(--text-light);
    font-family: "Open Sans", Arial, sans-serif;
    margin: 0;
    white-space: nowrap;
  }
  .company-name {
    top: 526px;
    font-size: 51px;
    font-weight: 700;
    letter-spacing: 0;
    line-height: 72px;
  }
  .person-name {
    top: 618px;
    font-size: 48px;
    font-weight: 400;
    line-height: 66px;
  }
</style>
</head>
<body>
<div class="canvas">
  <svg class="card-art" width="1200" height="1200" viewBox="0 0 1200 1200" xmlns="http://www.w3.org/2000/svg">
    <defs>
      <linearGradient id="card-green" x1="0" y1="0" x2="1" y2="0">
        <stop offset="0" stop-color="var(--green-deep)"/>
        <stop offset="0.35" stop-color="#14683a"/>
        <stop offset="0.7" stop-color="var(--green-mid)"/>
        <stop offset="1" stop-color="var(--green-bright)"/>
      </linearGradient>
      <radialGradient id="panel-dark" cx="0.5" cy="0.5" r="0.6">
        <stop offset="0" stop-color="var(--panel-centre)"/>
        <stop offset="1" stop-color="var(--panel-outer)"/>
      </radialGradient>
      <radialGradient id="ornament-glow" cx="0.5" cy="0.5" r="0.5">
        <stop offset="0" stop-color="#1f9a45" stop-opacity="0.75"/>
        <stop offset="0.7" stop-color="#0f6b31" stop-opacity="0.35"/>
        <stop offset="1" stop-color="#0f6b31" stop-opacity="0"/>
      </radialGradient>
      <linearGradient id="rule-fade" x1="0" y1="0" x2="1" y2="0">
        <stop offset="0" stop-color="#1f9a45"/>
        <stop offset="0.5" stop-color="#137a37"/>
        <stop offset="1" stop-color="#1f9a45"/>
      </linearGradient>
    </defs>

    <rect class="card-body" x="43" y="285" width="1114" height="630" fill="url(#card-green)"/>

    <polygon class="outer-frame"
      points="172,351 1029,351 1091,413 1091,787 1029,849 172,849 110,787 110,413"
      fill="none" stroke="var(--frame-line)" stroke-width="2"/>

    <polygon class="centre-panel"
      points="175,360 1026,360 1082,416 1082,784 1026,840 175,840 119,784 119,416"
      fill="url(#panel-dark)" stroke="var(--panel-edge)" stroke-width="3"/>

    <ellipse class="ornament-top" role="img" aria-label="Green scrolled filigree flourish above the company name"
      cx="600" cy="452" rx="295" ry="50" fill="url(#ornament-glow)"/>

    <rect class="rule-top" x="260" y="504" width="680" height="3" fill="url(#rule-fade)"/>
    <rect class="rule-bottom" x="260" y="693" width="680" height="3" fill="url(#rule-fade)"/>

    <ellipse class="ornament-bottom" role="img" aria-label="Green scrolled filigree flourish below the contact name"
      cx="600" cy="750" rx="295" ry="50" fill="url(#ornament-glow)"/>
  </svg>

  <h1 class="card-text company-name">COPPER LARK BUILDWORKS</h1>
  <p class="card-text person-name">Owen Tarrant</p>
</div>
</body>
</html>
```